MBRDC redesign and update stationary bc envelopes.

Stationary, Envelopes, Brochures, Business Card. Need to add second surgeon and two other offices. I need everything to match. I am a oral & maxillofacial surgeon.
Additional surgeon and three office addresses.
Jae Min Park, DMD, MD, INC

3718 Silver Meadow Parkway
Maple Ridge, CA 95712

642 Lorin Way, Suite 101
Cedar Falls, CA. 95644

2317 Vale Street, Suite 105
Brookline, CA. 95618
Updates

Logo design uploaded. Zapfino Extra/Adobe Garamond/Palatino are fonts used before. Not sure what is on exisiting stationary.

Target Market(s)

Referral dentist and sometimes patients. I am a oral & Maxillofacial surgeon.

Industry/Entity Type

Dental Clinic

Font styles to use
Serif
Script

Requirements
Must have
• Color of existing stationary. Update is possible.
Nice to have
• Conservative/modern
Should not have
• Playful

```html
<!DOCTYPE html>
<html lang="en">
<head>
<meta charset="utf-8">
<title>MBRDC Letterhead</title>
<link rel="stylesheet" href="https://fonts.googleapis.com/css2?family=EB+Garamond:ital,wght@0,400;0,500;1,400&display=swap">
<style>
  :root {
    --backdrop: #dcdcde;
    --paper: #fdfbee;
    --paper-low: #f6f1e4;
    --green: #6a9a2a;
    --brown: #634b3e;
    --ink: #4a3a32;
    --white: #ffffff;
  }
  * { box-sizing: border-box; margin: 0; padding: 0; }
  html, body {
    width: 1162px; height: 1200px; overflow: hidden;
    background: var(--backdrop);
  }
  .letterhead {
    position: absolute; left: 131px; top: 18px;
    width: 900px; height: 1164px;
    background: linear-gradient(180deg, var(--paper) 0%, var(--paper-low) 100%);
    font-family: "EB Garamond", Georgia, serif;
    color: var(--ink);
  }
  .brand {
    position: absolute; left: 72px; top: 150px;
    display: flex; align-items: center; gap: 14px;
  }
  .brand-dot {
    width: 26px; height: 26px; border-radius: 50%;
    background: var(--green);
  }
  .brand-name {
    font-size: 46px; font-weight: 500; letter-spacing: 3px;
    color: var(--brown); line-height: 1;
  }
  .contact {
    position: absolute; right: 64px; top: 48px;
    text-align: right; font-style: normal;
    font-size: 13.5px; line-height: 16px;
  }
  .contact .surgeon {
    font-style: italic; color: var(--green); font-size: 16px; line-height: 18px;
  }
  .contact .line { display: flex; justify-content: flex-end; align-items: center; gap: 4px; }
  .contact .icon { width: 11px; height: 11px; flex: none; }
  .contact .email { margin-top: 10px; padding-right: 18px; }
  .footer-rule {
    position: absolute; left: 0; right: 0; bottom: 86px;
    height: 3px; background: var(--green);
  }
  .footer-band {
    position: absolute; left: 0; right: 0; bottom: 0;
    height: 80px; background: var(--brown);
    display: flex; align-items: center; justify-content: center;
  }
  .footer-band .web {
    color: var(--white); font-style: italic; font-size: 22px; letter-spacing: 5px;
  }
</style>
</head>
<body>
  <main class="letterhead">
    <div class="brand">
      <span class="brand-dot"></span>
      <span class="brand-name">MBRDC</span>
    </div>

    <address class="contact">
      <div class="surgeon">Thomas E. Harlan, DDS, Inc.</div>
      <div class="surgeon">Jae Min Park, DMD, MD, Inc.</div>
      <div>3718 Silver Meadow Parkway</div>
      <div>Maple Ridge, CA 95712</div>
      <div>642 Lorin Way, Suite 101</div>
      <div>Cedar Falls, CA. 95644</div>
      <div>2317 Vale Street, Suite 105</div>
      <div>Brookline, CA. 95618</div>
      <div class="line">555.014.3927
        <svg class="icon" viewBox="0 0 12 12" aria-label="phone"><rect width="12" height="12" rx="2" fill="#6a9a2a"/><path d="M3 3.2c0 3 2.6 5.6 5.6 5.6l.8-1.4-1.6-.9-.7.7c-1-.4-1.8-1.2-2.2-2.2l.7-.7-.9-1.6z" fill="#fff"/></svg>
      </div>
      <div class="line">555.014.6381
        <svg class="icon" viewBox="0 0 12 12" aria-label="fax"><rect width="12" height="12" rx="2" fill="#6a9a2a"/><rect x="3" y="2.5" width="6" height="3" fill="#fff"/><rect x="2" y="5.5" width="8" height="4" rx="1" fill="#fff"/></svg>
      </div>
      <div class="line">meadowbrookoralsurgery.com
        <svg class="icon" viewBox="0 0 12 12" aria-label="email"><rect width="12" height="12" rx="2" fill="#6a9a2a"/><rect x="2" y="3.5" width="8" height="5" fill="#fff"/><path d="M2 3.5l4 3 4-3" stroke="#6a9a2a" stroke-width="0.8" fill="none"/></svg>
      </div>
      <div class="email">drharlan@meadowbrookoralsurgery.com</div>
    </address>

    <div class="footer-rule"></div>
    <footer class="footer-band">
      <span class="web">www.meadowbrookoralsurgery.com</span>
    </footer>
  </main>
</body>
</html>
```